Business Cards

Need business card design that I can update for new employees and details. Needs to incorporate our logo, be bright and fun (in line with tourism and holidays)
Would like a Map of Western Australia on the front with locations all the caravan parks we own (just purchased Tom Price so please include that as well as others listed on our website).
Target Market(s)
Famillies
Contact Information for Business Card
5 Cards -
Neil Perrow (Director) e: perrow@wattlebay.com.au p: 0491 570 156
Mira Perrow (Director) e: perrow@wattlebay.com.au p: 0491 570 157
Owen Halvey (General Manager) e: halvey@wattlebay.com.au p: 0491 570 158
Helen Halvey (General Manager) e: halvey@wattlebay.com.au p: 0491 570 159
Colin Danby (Training and Operations Manager) - e: danby@wattlebay.com.au p:0491 570 110
Colors
Look and feel

```html
<!DOCTYPE html>
<html lang="en">
<head>
<meta charset="utf-8">
<title>Wattlebay Tourist Parks – Business Cards</title>
<link rel="stylesheet" href="https://fonts.googleapis.com/css2?family=Roboto+Condensed:wght@400;700&display=swap">
<style>
  :root {
    --backdrop: #e9e6e1;
    --card: #ffffff;
    --frame: #3fbfd0;
    --sky: #4fc6d6;
    --sea: #6dbcaa;
    --ink: #4a4a4a;
    --accent: #3bbcd0;
    --accent-soft: #6cc6b7;
  }
  * { box-sizing: border-box; margin: 0; padding: 0; }
  html, body { width: 1200px; height: 886px; overflow: hidden; }
  body {
    background: var(--backdrop);
    display: flex;
    align-items: center;
    justify-content: center;
    gap: 60px;
    font-family: "Roboto Condensed", Arial, sans-serif;
  }
  .card {
    width: 520px;
    height: 318px;
    background: var(--card);
    position: relative;
    box-shadow: 0 6px 18px rgba(0,0,0,0.12);
  }

  /* Front */
  .card-front__frame {
    position: absolute;
    inset: 12px;
    border: 5px solid var(--frame);
  }
  .card-front__scene {
    position: absolute;
    top: 25px;
    right: 25px;
    width: 250px;
    height: 190px;
    background: linear-gradient(160deg, var(--sky) 0%, var(--sky) 45%, var(--sea) 100%);
  }
  .card-front__details {
    position: absolute;
    left: 32px;
    bottom: 28px;
    width: 200px;
  }
  .wordmark {
    font-family: "Roboto Condensed", Arial, sans-serif;
    font-weight: 400;
    color: var(--ink);
    font-size: 17px;
    line-height: 1.15;
    letter-spacing: 0.5px;
  }
  .person { margin-top: 18px; }
  .person__name {
    font-size: 19px;
    font-weight: 700;
    color: var(--accent);
    text-transform: uppercase;
    letter-spacing: 0.3px;
    line-height: 1.1;
  }
  .person__role {
    font-size: 12px;
    color: var(--accent-soft);
    text-transform: uppercase;
    margin-top: 2px;
  }
  .contact {
    margin-top: 12px;
    font-size: 13px;
    line-height: 1.35;
    color: var(--ink);
    list-style: none;
  }
  .contact strong { font-weight: 700; }

  /* Back */
  .card-back__brand {
    position: absolute;
    top: 130px;
    left: 0;
    right: 0;
    display: flex;
    align-items: center;
    justify-content: center;
    gap: 14px;
  }
  .card-back .wordmark { font-size: 24px; }
  .brand-square {
    width: 34px;
    height: 34px;
    background: var(--sea);
  }
  .card-back__web {
    position: absolute;
    top: 186px;
    left: 0;
    right: 0;
    text-align: center;
    font-size: 12px;
    color: var(--ink);
    letter-spacing: 0.3px;
  }
</style>
</head>
<body>
  <article class="card card-front">
    <div class="card-front__frame"></div>
    <div class="card-front__scene" role="img" aria-label="Sunburst rising over a sweeping sea-green hill with birds in a teal sky"></div>
    <div class="card-front__details">
      <div class="wordmark">Wattlebay<br>Tourist Parks</div>
      <div class="person">
        <div class="person__name">Neil Perrow</div>
        <div class="person__role">Director</div>
      </div>
      <ul class="contact">
        <li><strong>Phone:</strong> 0491 570 156</li>
        <li>perrow@wattlebay.com.au</li>
        <li>www.wattlebay.com.au</li>
      </ul>
    </div>
  </article>

  <article class="card card-back">
    <div class="card-back__brand">
      <div class="wordmark">Wattlebay Tourist Parks</div>
      <div class="brand-square"></div>
    </div>
    <div class="card-back__web">www.wattlebay.com.au</div>
  </article>
</body>
</html>
```